Brivolt Technologies business card design

We need a business card designed with our new logo. it would be great if the card could communicate it is a technology based company.

Target Market(s)

system integrators

Industry/Entity Type

technology, IOT

Contact Information for Business Card

Name, designation, Address, telephone number, email address

Requirements
Must have
• logo and company name
Nice to have
• something to do with technology

```html
<!DOCTYPE html>
<html lang="en">
<head>
<meta charset="utf-8">
<title>Brivolt Technologies – Business Card</title>
<link rel="stylesheet" href="https://fonts.googleapis.com/css2?family=Poppins:wght@400;500;700&display=swap">
<style>
  :root {
    --canvas: #1c1c1c;
    --charcoal: #3d3d3f;
    --orange: #f39322;
    --white: #ffffff;
    --ink: #2f2f31;
  }
  * { box-sizing: border-box; margin: 0; padding: 0; }
  html, body { width: 1200px; height: 852px; overflow: hidden; }
  body {
    background: var(--canvas);
    font-family: "Poppins", sans-serif;
    display: flex; flex-direction: column; align-items: center; justify-content: center; gap: 34px;
  }
  .card {
    position: relative; width: 660px; height: 377px; overflow: hidden;
    box-shadow: 0 10px 30px rgba(0,0,0,.5);
  }
  .card-front { background: var(--charcoal); display: flex; align-items: center; justify-content: center; }
  .wordmark { display: flex; align-items: center; gap: 16px; }
  .wordmark-square { width: 34px; height: 34px; background: var(--orange); }
  .wordmark-name { font-weight: 700; font-size: 40px; letter-spacing: 1px; text-transform: uppercase; line-height: 1; }
  .card-front .wordmark-name { color: var(--white); }
  .card-back { background: var(--white); }
  .card-back .shapes { position: absolute; inset: 0; }
  .card-back .wordmark { position: absolute; left: 40px; top: 128px; gap: 12px; }
  .card-back .wordmark-name { color: var(--ink); font-size: 30px; }
  .card-back .wordmark-square { width: 24px; height: 24px; }
  .holder { position: absolute; right: 58px; top: 38px; text-align: right; }
  .holder-name { color: var(--orange); font-weight: 700; font-size: 24px; text-transform: uppercase; line-height: 1.1; }
  .holder-title { color: var(--ink); font-size: 14px; text-transform: uppercase; letter-spacing: 1px; }
  .address { position: absolute; left: 40px; top: 196px; color: var(--ink); font-size: 15px; line-height: 1.35; }
  .contacts { position: absolute; left: 40px; top: 280px; list-style: none; color: var(--white); font-size: 15px; line-height: 1.5; }
  .contacts li { display: flex; align-items: center; gap: 10px; }
  .contacts svg { width: 13px; height: 13px; flex: none; }
</style>
</head>
<body>
  <section class="card card-front">
    <div class="wordmark">
      <span class="wordmark-square"></span>
      <span class="wordmark-name">Brivolt Technologies</span>
    </div>
  </section>

  <section class="card card-back">
    <svg class="shapes" viewBox="0 0 660 377" width="660" height="377">
      <polygon points="470,125 660,55 660,250 575,292" fill="var(--orange)"/>
      <polygon points="0,262 340,215 575,305 660,268 660,377 0,377" fill="var(--charcoal)"/>
      <rect x="532" y="150" width="58" height="58" fill="var(--charcoal)"/>
      <rect x="628" y="30" width="14" height="30" fill="var(--orange)"/>
    </svg>

    <div class="holder">
      <div class="holder-name">Daniel Rourke</div>
      <div class="holder-title">Director</div>
    </div>

    <div class="wordmark">
      <span class="wordmark-square"></span>
      <span class="wordmark-name">Brivolt Technologies</span>
    </div>

    <p class="address">414 Linden Crest Road<br>Harlow Falls, MI 48120</p>

    <ul class="contacts">
      <li>
        <svg viewBox="0 0 16 16"><path d="M3 1h3l1.5 4-2 1.2a9 9 0 0 0 4.3 4.3L11 8.5l4 1.5v3a2 2 0 0 1-2 2A12 12 0 0 1 1 3a2 2 0 0 1 2-2z" fill="var(--orange)"/></svg>
        (555) 318-4072
      </li>
      <li>
        <svg viewBox="0 0 16 16"><rect x="1" y="3" width="14" height="10" fill="none" stroke="var(--orange)" stroke-width="1.6"/><path d="M1 3l7 6 7-6" fill="none" stroke="var(--orange)" stroke-width="1.6"/></svg>
        info@brivolttech.com
      </li>
      <li>
        <svg viewBox="0 0 16 16"><circle cx="8" cy="8" r="6.5" fill="none" stroke="var(--orange)" stroke-width="1.5"/><path d="M1.5 8h13M8 1.5c-3 3.5-3 9.5 0 13M8 1.5c3 3.5 3 9.5 0 13" fill="none" stroke="var(--orange)" stroke-width="1.2"/></svg>
        brivolttech.com
      </li>
    </ul>
  </section>
</body>
</html>
```